Bork Ventures, Inc. Website redesign

Revamp the website, it is old and outdated. www.borkventuresinc.example

Target Market(s)

Information Technology Consulting and Staffing

Coding

Coded - Design and coding required

Number of Pages Required

5+ page

Colors

Designer to choose colors to be used in the design.

Requirements
Must have
• Outlined text boxes just like from the Tolvane.example site. A clean look

```html
<!DOCTYPE html>
<html lang="en">
<head>
<meta charset="utf-8">
<title>Bork Ventures, Inc. | Home</title>
<link href="https://fonts.googleapis.com/css2?family=Mulish:wght@400;600;700;800&display=swap" rel="stylesheet">
<style>
:root{
  --brand:#8c1230;
  --ink:#1e1e1e;
  --text:#333;
  --muted:#555;
  --band:#e8e8e8;
  --card:#fff;
  --dark:#1d1c1e;
  --rule:#bbb;
}
*{box-sizing:border-box;margin:0;padding:0}
html,body{width:1200px;height:3494px;overflow:hidden}
body{position:relative;font-family:"Mulish",sans-serif;color:var(--text);background:#fff}
.abs{position:absolute}
.center{left:0;width:1200px;text-align:center}

/* header */
.site-header{top:0;left:0;width:1200px;height:80px;background:#fff}
.brand{left:144px;top:24px}
.brand-name{font-weight:800;font-size:24px;color:var(--brand);letter-spacing:1px}
.nav{top:33px;left:582px;display:flex;gap:33px;font-size:13px;color:#222}
.nav .active{color:var(--brand);border-bottom:2px solid var(--brand);padding-bottom:3px}

/* hero */
.hero-art{top:80px;left:0;width:1200px;height:650px;clip-path:polygon(0 0,100% 0,100% 537px,50% 650px,0 537px);
  background:radial-gradient(ellipse at 52% 40%,#f4e6c4 0%,#a99f93 35%,#50535a 70%,#2a2c30 100%)}
.hero-caption{top:297px;left:272px;width:656px;height:95px;background:rgba(40,40,40,.78);color:#fff;
  font-weight:700;font-size:32px;line-height:41px;text-align:center;padding-top:7px}
.hero-arrow{top:327px;width:40px;height:40px;background:var(--brand)}
.hero-arrow svg{display:block}

/* section headings */
.section-title{font-weight:800;font-size:34px;color:var(--brand);letter-spacing:.3px}
.rule{left:558px;width:122px;height:3px;background:var(--ink)}

.lead{font-size:16px;line-height:26px;color:#222}
.small{font-size:11.5px;line-height:22.5px;color:#444}

/* bands */
.band{left:0;width:1200px;background:var(--band)}

/* service cards */
.service-card{top:1239px;width:216px;height:359px;background:var(--card)}
.service-photo{width:216px;height:159px}
.service-badge{top:119px;left:68px;width:80px;height:80px;border-radius:50%;background:var(--brand);display:flex;align-items:center;justify-content:center}
.service-title{top:210px;left:0;width:216px;text-align:center;font-size:19.5px;line-height:24px;font-weight:400;color:var(--brand)}
.service-desc{top:269px;left:14px;width:188px;text-align:center;font-size:10.5px;line-height:17.5px;color:#333}

/* strategy */
.step{top:1982px;width:120px;text-align:center}
.step-label{font-size:19px;color:#222;margin-top:8px}
.step-arrow{top:2004px;height:2px;background:#c9c9c9}
.step-arrow::after{content:"";position:absolute;right:-2px;top:-4px;border-left:8px solid #c9c9c9;border-top:5px solid transparent;border-bottom:5px solid transparent}
.button{background:var(--brand);color:#fff;font-size:13px;text-align:center;line-height:40px;letter-spacing:.3px}

/* news */
.news-card{top:2369px;width:298px;height:123px;background:#fff;border-bottom:3px solid var(--brand);padding:17px 18px}
.news-date{font-size:13px;color:var(--brand)}
.news-text{font-size:12.5px;line-height:19px;color:#333;margin-top:10px}

/* contact */
.contact-info{top:2826px;left:144px;width:456px;height:387px;background:var(--band)}
.contact-map{top:2826px;left:600px;width:456px;height:387px;background:linear-gradient(135deg,#eef0f1,#e2e6e8 60%,#dfe8d8)}
.contact-row{left:50px;display:flex;gap:14px;font-size:21px;line-height:29px;color:#222;white-space:nowrap}
.contact-row svg{flex:none;margin-top:7px}
.social-ring{top:264px;width:56px;height:56px;border-radius:50%;border:1.5px solid #555}

/* footer */
.site-footer{top:3296px;left:0;width:1200px;height:198px;background:var(--dark);clip-path:polygon(0 104px,50% 0,100% 104px,100% 100%,0 100%)}
.footer-links{top:3410px;left:144px;font-size:11px;color:#aaa}
.footer-links span{margin:0 7px}
.copyright{top:3441px;left:144px;font-size:11px;color:#aaa}
.footer-dot{top:3428px;width:14px;height:14px;border-radius:50%;background:#9a9aa0}
</style>
</head>
<body>

<header class="abs site-header">
  <div class="abs brand"><span class="brand-name">BORK VENTURES</span></div>
  <nav class="abs nav"><span class="active">Home</span><span>About Us</span><span>Services</span><span>Strategy</span><span>IT News</span><span>Contact Us</span></nav>
</header>

<section>
  <div class="abs hero-art" role="img" aria-label="Close-up photograph of a network router on a desk with a person working at a laptop behind it"></div>
  <div class="abs hero-caption">BRINGING THOUGHT LEADERSHIP AND<br>QUALITY TO EVERY PROJECT</div>
  <div class="abs hero-arrow" style="left:47px"><svg width="40" height="40"><path d="M23 12l-8 8 8 8" fill="none" stroke="#fff" stroke-width="4"/></svg></div>
  <div class="abs hero-arrow" style="left:1112px"><svg width="40" height="40"><path d="M17 12l8 8-8 8" fill="none" stroke="#fff" stroke-width="4"/></svg></div>
</section>

<section>
  <h1 class="abs center section-title" style="top:801px">WELCOME TO BORK VENTURES</h1>
  <div class="abs rule" style="top:854px"></div>
  <p class="abs lead" style="top:868px;left:144px;width:912px;text-align:center">Bork Ventures, Inc. is an 8(a) full-service IT consulting company based in the Washington, DC Metro area. We offer specialized, highly customized technology solutions for our customers located throughout the United States.</p>
  <p class="abs small" style="top:929px;left:150px;width:900px;text-align:center">No two businesses are the same. We believe the technology supporting your business operations should align with your company. Every project begins with a thorough analysis of your current technology environment. We work with you to define the environment you want. Then we implement industry-proven practices that enable you to achieve your business objectives. We draw on our experience at civilian and federal agencies to generate ideas and create IT solutions that address your unique business needs. Learn about our Strategies.</p>
</section>

<section>
  <div class="abs band" style="top:1096px;height:650px;clip-path:polygon(0 0,100% 0,100% 536px,50% 650px,0 536px)"></div>
  <h2 class="abs center section-title" style="top:1166px">OUR SERVICES</h2>
  <div class="abs rule" style="top:1219px"></div>

  <article class="abs service-card" style="left:144px">
    <div class="service-photo" role="img" aria-label="Photograph of a circuit board" style="background:linear-gradient(135deg,#2f4a66,#14263a)"></div>
    <div class="abs service-badge"><svg width="40" height="40" fill="none" stroke="#fff" stroke-width="2"><rect x="6" y="7" width="26" height="18"/><path d="M14 13l-4 3 4 3M24 13l4 3-4 3M21 12l-4 9M14 31h12M20 25v6"/><circle cx="31" cy="30" r="4"/></svg></div>
    <h3 class="abs service-title">HARDWARE /<br>SOFTWARE SALES</h3>
    <p class="abs service-desc">IT support offering, we simplify the IT implementation process while insuring your ability to get best pricing.</p>
  </article>

  <article class="abs service-card" style="left:376px">
    <div class="service-photo" role="img" aria-label="Photograph of a desktop monitor showing a file transfer screen" style="background:linear-gradient(180deg,#1d2b52,#2d3f73 60%,#d6d6d6 60%)"></div>
    <div class="abs service-badge"><svg width="40" height="40" fill="none" stroke="#fff" stroke-width="2"><path d="M13 17v-4a7 7 0 0 1 14 0v4"/><rect x="10" y="17" width="20" height="17" rx="3"/><circle cx="20" cy="25.5" r="3"/></svg></div>
    <h3 class="abs service-title">PROFESSIONAL<br>SERVICES</h3>
    <p class="abs service-desc">Virtualization<br>Messaging<br>Security<br>Disaster Recovery/Business Continuity</p>
  </article>

  <article class="abs service-card" style="left:608px">
    <div class="service-photo" role="img" aria-label="Photograph of a technician checking server racks" style="background:linear-gradient(90deg,#3a3632,#8d8a86 50%,#403c38)"></div>
    <div class="abs service-badge"><svg width="40" height="40" fill="none" stroke="#fff" stroke-width="2"><path d="M13 17a5 5 0 0 1 3-8 6 6 0 0 1 11 2 4 4 0 0 1 0 8H14z"/><path d="M20 19v5M9 24h22M9 24v4M20 24v4M31 24v4"/><rect x="5" y="28" width="8" height="6"/><rect x="16" y="28" width="8" height="6"/><rect x="27" y="28" width="8" height="6"/></svg></div>
    <h3 class="abs service-title">TECHNOLOGY<br>ASSESSMENT</h3>
    <p class="abs service-desc">Network Assessment<br>Infrastructure Analysis<br>Health Checks<br>Performance Analysis</p>
  </article>

  <article class="abs service-card" style="left:840px">
    <div class="service-photo" role="img" aria-label="Photograph of a consultant planning on a whiteboard" style="background:linear-gradient(90deg,#5a6070,#c9ccd2 45%,#8e9099)"></div>
    <div class="abs service-badge"><svg width="40" height="40" fill="none" stroke="#fff" stroke-width="2"><rect x="13" y="5" width="14" height="11"/><path d="M16 9h8M16 12h8M20 16v5M9 21h22M9 21v5M20 21v5M31 21v5"/><rect x="5" y="26" width="8" height="8"/><rect x="16" y="26" width="8" height="8"/><rect x="27" y="26" width="8" height="8"/></svg></div>
    <h3 class="abs service-title">TECHNOLOGY<br>CONSULTING</h3>
    <p class="abs service-desc">Project Management<br>Business Improvement<br>Staffing Solutions</p>
  </article>
</section>

<section>
  <h2 class="abs center section-title" style="top:1818px">OUR STRATEGY</h2>
  <div class="abs rule" style="top:1871px"></div>
  <p class="abs small" style="top:1887px;left:144px;width:912px;text-align:center">Civilian and Federal agencies are facing increased demands driven by the changing economic environment and shifts in the way products and services are sold and delivered. These factors have created an imperative to leverage new and innovative technology solution architectures like cloud computing to help reduce cost and deliver profit-driving IT capabilities faster than ever before.</p>

  <div class="abs step" style="left:164px"><svg width="40" height="40" fill="none" stroke="var(--brand)" stroke-width="5"><circle cx="17" cy="17" r="11"/><path d="M25 25l11 11"/></svg><div class="step-label">Assess</div></div>
  <div class="abs step-arrow" style="left:268px;width:100px"></div>
  <div class="abs step" style="left:352px"><svg width="40" height="40" fill="var(--brand)"><path d="M4 12h9a5 5 0 1 1 8 0h9v9a5 5 0 1 1 0 8v9H4z"/></svg><div class="step-label">Recommend</div></div>
  <div class="abs step-arrow" style="left:452px;width:100px"></div>
  <div class="abs step" style="left:540px"><svg width="44" height="40" fill="none" stroke="var(--brand)" stroke-width="5" stroke-dasharray="4 3"><circle cx="16" cy="22" r="9"/><circle cx="34" cy="12" r="5"/><circle cx="34" cy="32" r="4"/></svg><div class="step-label">Implement</div></div>
  <div class="abs step-arrow" style="left:644px;width:100px"></div>
  <div class="abs step" style="left:728px"><svg width="46" height="40"><path d="M2 20q21-22 42 0q-21 22-42 0z" fill="none" stroke="var(--brand)" stroke-width="4"/><circle cx="23" cy="20" r="7" fill="var(--brand)"/></svg><div class="step-label">Monitor</div></div>
  <div class="abs step-arrow" style="left:832px;width:100px"></div>
  <div class="abs step" style="left:916px"><svg width="40" height="40"><path d="M8 34l16-16" stroke="var(--brand)" stroke-width="6" stroke-linecap="round"/><circle cx="28" cy="12" r="8" fill="var(--brand)"/><circle cx="32" cy="8" r="4" fill="#fff"/></svg><div class="step-label">Manage</div></div>

  <div class="abs button" style="top:2098px;left:540px;width:120px">READ MORE</div>
</section>

<section>
  <div class="abs band" style="top:2217px;height:458px;clip-path:polygon(0 0,100% 0,100% 338px,50% 458px,0 338px)"></div>
  <h2 class="abs center section-title" style="top:2287px">IT NEWS</h2>
  <div class="abs rule" style="top:2340px"></div>
  <article class="abs news-card" style="left:144px"><div class="news-date">4 September, 2019</div><p class="news-text">Etiam elementum, bibendum tellus venenatis, feugiat massa sollicitudin cursus dui eu.</p></article>
  <article class="abs news-card" style="left:451px"><div class="news-date">4 September, 2019</div><p class="news-text">Quisque aliquet nec est vestibulum pulvinar. Pellentesque convallis m olestie enim sit amet efficitur.</p></article>
  <article class="abs news-card" style="left:758px"><div class="news-date">4 September, 2019</div><p class="news-text">Vivamus lacus justo, ultrices nec erat in, euismod iaculis mauris. Vivamus eleifend vitae nulla malesuada.</p></article>
  <div class="abs button" style="top:2527px;left:528px;width:144px">VIEW ALL NEWS</div>
</section>

<section>
  <h2 class="abs center section-title" style="top:2748px">CONTACT INFO</h2>
  <div class="abs rule" style="top:2801px"></div>
  <div class="abs contact-info">
    <div class="abs contact-row" style="top:42px"><svg width="12" height="16"><path d="M6 16C2 10 1 8 1 6a5 5 0 0 1 10 0c0 2-1 4-5 10z" fill="#222"/><circle cx="6" cy="6" r="2" fill="var(--band)"/></svg><span>2840 Harlow Creek Rd<br>Ashcombe, MD 20991</span></div>
    <div class="abs contact-row" style="top:130px"><svg width="14" height="14"><path d="M3 1l3 3-2 2q2 4 4 4l2-2 3 3-2 2Q5 13 1 3z" fill="#222"/></svg><span>Phone : 555-014-2290</span></div>
    <div class="abs contact-row" style="top:188px"><svg width="16" height="12"><rect width="16" height="12" fill="#222"/><path d="M0 0l8 6 8-6" stroke="var(--band)" stroke-width="1.5" fill="none"/></svg><span>Email : info@borkventures.example</span></div>
    <div class="abs social-ring" style="left:50px"></div>
    <div class="abs social-ring" style="left:121px"></div>
    <div class="abs social-ring" style="left:193px"></div>
  </div>
  <div class="abs contact-map" role="img" aria-label="Street map showing the office location"></div>
</section>

<footer>
  <div class="abs site-footer"></div>
  <div class="abs footer-links">Home<span>|</span>About Us<span>|</span>Services<span>|</span>Strategy<span>|</span>IT News<span>|</span>Contact Us</div>
  <div class="abs copyright">Copyright © 2019 Bork Ventures. All rights reserved.</div>
  <div class="abs footer-dot" style="left:952px"></div>
  <div class="abs footer-dot" style="left:999px"></div>
  <div class="abs footer-dot" style="left:1042px"></div>
</footer>

</body>
</html>
```